Preisliste für Kosmetikinstitut
Zielgruppe
Ich benötige für mein Kosmetikinstitut eine Preisliste für die moderne Frau, aber auch Männer. Das Design sollte mein Logo enthalten. Farben des Designkonzepts einbauen.
A4 quer zum Falten, wie ein Heft, 1. Seite Preisliste mit logo, im Innenteil dann Anwendungen
Aufgabenstellung
Minimalistisch, ästhetisch, modern, edel
Kontaktdaten auf der Rückseite
LB Hautatelier
Lotte Brenner
Lindenhang 17
83671 Waakirchen
EMail: lotte@lb-hautatelier.de
Whatsapp: 0176 284 9017

```html
<!DOCTYPE html>
<html lang="de">
<head>
<meta charset="utf-8">
<title>Preisliste Gesichtsbehandlungen</title>
<link rel="stylesheet" href="https://fonts.googleapis.com/css2?family=Alegreya+Sans:wght@400;500;700&display=swap">
<style>
  :root {
    --ink: #5f6e6b;
    --panel: #eeedeb;
    --paper: #ffffff;
    --photo-light: #cfdde4;
    --photo-skin: #d6b7a2;
  }
  * { margin: 0; padding: 0; box-sizing: border-box; }
  html, body { width: 1200px; height: 848px; overflow: hidden; background: var(--paper); }
  body {
    position: relative;
    font-family: "Alegreya Sans", "Candara", sans-serif;
    color: var(--ink);
    font-variant-numeric: oldstyle-nums;
  }
  .panel {
    position: absolute; left: 27px; top: 28px; width: 547px; height: 793px;
    background: var(--panel);
  }
  .section-title {
    position: absolute; left: 142px; top: 134px;
    font-size: 20.5px; font-weight: 500; letter-spacing: 1.8px; line-height: 26px;
  }
  .treatment { position: absolute; width: 340px; }
  .treatment.left { left: 142px; }
  .treatment.right { left: 732px; }
  .treatment h3 {
    position: relative;
    font-size: 15.5px; font-weight: 700; letter-spacing: 1.7px;
    line-height: 20px; text-transform: uppercase; white-space: nowrap;
  }
  .treatment .price {
    position: absolute; white-space: nowrap;
    font-size: 16.5px; font-weight: 700; letter-spacing: 1.1px;
  }
  .treatment.left .price { left: 257px; }
  .treatment.right .price { left: 258px; }
  .treatment p {
    margin-top: 5px;
    font-size: 15px; line-height: 20px; letter-spacing: 0.25px;
    white-space: nowrap;
  }
  .photo { position: absolute; }
  .photo-tall {
    left: 527px; top: 511px; width: 171px; height: 337px;
    background: linear-gradient(100deg, var(--photo-light) 0%, var(--photo-skin) 55%, #c9a793 100%);
  }
  .photo-short {
    left: 705px; top: 658px; width: 171px; height: 190px;
    background: linear-gradient(260deg, var(--photo-light) 0%, var(--photo-skin) 60%, #cdab96 100%);
  }
</style>
</head>
<body>
  <div class="panel"></div>

  <h2 class="section-title">GESICHTSBEHANDLUNGEN</h2>

  <section class="treatment left" style="top:188px">
    <h3>Express Facial Treatment <span class="price" style="top:0">€ 59,00</span></h3>
    <p>Für alle, die wenig Zeit haben und trotzdem ihre<br>Haut auffrischen und revitalisieren wollen.<br>Reinigung, Enzympeeling, Serum, Maske,<br>Abschlusspflege; 35-45min</p>
  </section>

  <section class="treatment left" style="top:312px">
    <h3>Classic Facial Treatment <span class="price" style="top:0">€ 89,00</span><br>Klassische Gesichtsbehandlung</h3>
    <p>Reinigung, Enzympeeling, Vapozon, Ausreinigung,<br>Augenbrauenkorrektur, Ampulle, Maske,individuelle<br>Abschlusspflege; 45-60min</p>
  </section>

  <section class="treatment left" style="top:436px">
    <h3>Clear Skin Treatment <span class="price" style="top:0">€ 89,00</span></h3>
    <p>Die Haut wirkt ausgeglichener, Unreinheiten wird<br>vorgebeugt, der Teint erhält Balance und kann sich<br>beruhigen. Gleichzeitig wird die Haut durch die<br>Hyaluronsäure vitalisiert und Falten und Fältchen<br>kann entgegengewirkt werden. 50-60min</p>
  </section>

  <section class="treatment left" style="top:580px">
    <h3>Capiluna Treatment <span class="price" style="top:0">€ 89,00</span></h3>
    <p>Hautrötungen und Couperose Erscheinungen wer-<br>den gelindert, die Gefäßwände werden gestärkt und<br>das Hautbild wirkt ausgeglichener, mögliche Irritati-<br>onen gehen zurück. Gleichzeitig sorgt die hochkon-<br>zentrierte Hyaluronsäure für Frische, Vitalität und<br>Glätte; 50-60min</p>
  </section>

  <section class="treatment right" style="top:58px">
    <h3>Sensora Soft Treatment <span class="price" style="top:0">€ 79,00</span><br>(für die empfindliche, gereizte Haut)</h3>
    <p>Entzündliche Prozesse können gemildert werden,<br>gereizte Haut oder solche, die wenig verträgt, wird<br>beruhigt. Irritationen können zurückgehen, die Haut<br>erhält Balance.&nbsp; ca 50min</p>
  </section>

  <section class="treatment right" style="top:204px">
    <h3>Vitamin Soft Boost <span class="price" style="top:0">€ 79,00</span></h3>
    <p>Vitamine sorgen für Power und Frische in<br>und auf der Haut, die Widerstandskraft der<br>Haut wird gestärkt. Die Faltentiefe kann ge-<br>mildert werden. ca. 50min</p>
  </section>

  <section class="treatment right" style="top:328px">
    <h3>Anti-Age Advanced <span class="price" style="top:0">€ 99,00</span></h3>
    <p>Die Haut wirkt insgesamt erfrischt,<br>vitalisiert und gestrafft. Feine Linien<br>und Fältchen werden reduziert.<br>50-70min (je nach Peeling)</p>
  </section>

  <section class="treatment right" style="top:452px">
    <h3>Chemisches Peeling<br>(Oktober – April) <span class="price" style="top:20px">€ 89,00</span></h3>
    <p>Professionelle Peelings können viele<br>Problemstellungen lindern, verbessern<br>oder gar beheben. Dazu gehören die<br>Zellerneuerung, Glättung der Hauttextur,<br>Reduzierung von Pigmentflecken, Ver-<br>besserung von Akne</p>
  </section>

  <div class="photo photo-tall" role="img" aria-label="Porträtfoto einer Frau mit gepflegter Haut, linke Gesichtshälfte, vor hellblauem Hintergrund"></div>
  <div class="photo photo-short" role="img" aria-label="Porträtfoto, rechte Gesichtshälfte mit Hand an der Wange, vor hellblauem Hintergrund"></div>
</body>
</html>
```